Heritage Hollow Business Cards

Require a business card design. <br/><br/>Needs to include logo (either round or long version) plus these details:<br/>Maya Torvell<br/>Heritage Hollow<br/>maya@kelvadtrading.com.au<br/>02 6481 7395<br/>PO Box Glenwarra NSW 2791<br/>www.heritagehollow.com.au<br/><br/>I need in an editable format so that I can create for multiple staff members. <br/><br/>

Target Market(s)

We are an online store selling renovation products to home owners are builders. Looking for a classic classy design.

Industry/Entity Type

Home And Garden

Contact Information for Business Card

Maya Torvell
Heritage Hollow
maya@kelvadtrading.com.au
02 6481 7395
PO Box Glenwarra NSW 2791
www.heritagehollow.com.au

Colors

Designer to choose colors to be used in the design.

Requirements
Must have
• Must include Logo.

```html
<!DOCTYPE html>
<html lang="en">
<head>
<meta charset="utf-8">
<title>Heritage Hollow Business Cards</title>
<link href="https://fonts.googleapis.com/css2?family=Roboto:wght@400;500;700&display=swap" rel="stylesheet">
<style>
  :root {
    --page: #e9e7e4;
    --card-dark: #2b2828;
    --card-light: #ffffff;
    --ink: #1f1d1d;
    --ink-soft: #3a3838;
    --on-dark: #f4f2f0;
  }
  * { box-sizing: border-box; margin: 0; padding: 0; }
  html, body { width: 1200px; height: 900px; overflow: hidden; }
  body {
    background: var(--page);
    font-family: "Roboto", sans-serif;
    color: var(--ink);
    position: relative;
  }
  .card {
    position: absolute;
    left: 250px;
    width: 700px;
    height: 400px;
    border-radius: 22px;
    overflow: hidden;
    box-shadow: 0 6px 18px rgba(0,0,0,0.18);
  }
  /* back */
  .card--back { top: 35px; background: var(--card-dark); }
  .back-seal {
    position: absolute;
    left: 230px; top: 80px;
    width: 240px; height: 240px;
    border: 1.5px solid var(--on-dark);
    border-radius: 50%;
    display: flex; align-items: center; justify-content: center;
  }
  .back-seal__name {
    color: var(--on-dark);
    font-size: 30px;
    font-weight: 500;
    text-align: center;
    line-height: 1.15;
  }
  /* front */
  .card--front { top: 465px; background: var(--card-light); }
  .front-brand {
    position: absolute;
    right: 60px; top: 62px;
    display: flex; align-items: center; gap: 14px;
  }
  .front-brand__mark {
    width: 54px; height: 54px;
    border: 1.5px solid var(--ink);
    border-radius: 50%;
  }
  .front-brand__name { font-size: 36px; font-weight: 500; color: var(--ink); }
  .divider {
    position: absolute;
    height: 2px;
    background: var(--ink);
  }
  .divider--top { left: 360px; right: 50px; top: 170px; height: 1.5px; }
  .divider--bottom { left: 110px; right: 50px; top: 336px; }
  .side-tab {
    position: absolute;
    left: 0; top: 212px;
    width: 14px; height: 44px;
    background: var(--card-dark);
    border-radius: 0 6px 6px 0;
  }
  .person { position: absolute; left: 50px; top: 188px; }
  .person__name { font-size: 27px; font-weight: 700; color: var(--ink); }
  .person__company { font-size: 17px; font-weight: 500; color: var(--ink-soft); margin-top: 2px; margin-left: 16px; }
  .contact-list {
    position: absolute; left: 104px; top: 256px;
    list-style: none;
  }
  .contact-list li {
    display: flex; align-items: center; gap: 8px;
    font-size: 20px; color: var(--ink-soft);
    height: 26px;
  }
  .contact-list svg { width: 16px; height: 16px; fill: var(--ink); flex: none; }
  .address {
    position: absolute; left: 120px; top: 348px;
    display: flex; align-items: center; gap: 12px;
    font-size: 20px; color: var(--ink-soft);
  }
  .address svg { width: 18px; height: 24px; fill: var(--ink); }
</style>
</head>
<body>

<section class="card card--back">
  <div class="back-seal">
    <p class="back-seal__name">Heritage<br>Hollow</p>
  </div>
</section>

<section class="card card--front">
  <div class="front-brand">
    <span class="front-brand__mark"></span>
    <span class="front-brand__name">Heritage Hollow</span>
  </div>
  <div class="divider divider--top"></div>

  <div class="side-tab"></div>

  <div class="person">
    <p class="person__name">Maya Torvell</p>
    <p class="person__company">Heritage Hollow</p>
  </div>

  <ul class="contact-list">
    <li>
      <svg viewBox="0 0 24 24"><path d="M6.6 10.8a15.1 15.1 0 0 0 6.6 6.6l2.2-2.2c.3-.3.7-.4 1-.2 1.1.4 2.3.6 3.6.6.6 0 1 .4 1 1V20c0 .6-.4 1-1 1A17 17 0 0 1 3 4c0-.6.4-1 1-1h3.5c.6 0 1 .4 1 1 0 1.3.2 2.5.6 3.6.1.3 0 .7-.2 1z"/></svg>
      02 6481 7395
    </li>
    <li>
      <svg viewBox="0 0 24 24"><path d="M2 5h20v14H2z M4 7v.5l8 5 8-5V7l-8 5z" fill-rule="evenodd"/></svg>
      maya@kelvadtrading.com.au
    </li>
    <li>
      <svg viewBox="0 0 24 24"><circle cx="12" cy="12" r="10"/><path d="M12 2v20M2 12h20" stroke="#fff" stroke-width="1.5"/></svg>
      www.heritagehollow.com.au
    </li>
  </ul>

  <div class="divider divider--bottom"></div>

  <div class="address">
    <svg viewBox="0 0 18 24"><path d="M9 0a9 9 0 0 0-9 9c0 6.5 9 15 9 15s9-8.5 9-15a9 9 0 0 0-9-9zm0 12.5A3.5 3.5 0 1 1 9 5.5a3.5 3.5 0 0 1 0 7z"/></svg>
    PO Box Glenwarra NSW 2791
  </div>
</section>

</body>
</html>
```